Webshop for furniture and lamps

We need a design for a web shop with APP that should have two options:
1-Webshop in general which should attract to private customer in general and
2-Website that is meant to attract big customers as hotels and restaurants who would have their own customerize login.

That's the idea behind the shop.

It should be diveded into 4 parts
vintage furniture
rattan set outdoor and indoor
lamps and
wooden wall decor

The name of the shop is loma vereda!

Please kindly make me an offer.

Reason: Dear designers, so far there hasn't been a design that really matched. Look up German web sites like www.glimmerhof-wohnen.de or www.sitzraum77.de... Haven't been convinced by designs! Sorry folks. Please submit some new ones. Kind regards Ned

```html
<!DOCTYPE html>
<html lang="en">
<head>
<meta charset="utf-8">
<title>Loma Vereda – Furniture &amp; Lamps</title>
<link href="https://fonts.googleapis.com/css2?family=Open+Sans:wght@400;600;700;800&display=swap" rel="stylesheet">
<style>
:root{
  --teal:#1fb5a8;
  --teal-dark:#179a8f;
  --dark:#3b3b3b;
  --panel:#4a4a4a;
  --ink:#333;
  --muted:#888;
  --price:#d0322d;
  --orange:#f08a2c;
  --btn:#b5ada0;
  --beige:#f1eee7;
  --line:#d9d9d9;
  --white:#fff;
}
*{box-sizing:border-box;margin:0;padding:0}
html,body{width:1200px;height:2851px;overflow:hidden}
body{font-family:"Open Sans",Arial,sans-serif;color:var(--ink);background:var(--white);position:relative;font-size:12px}
.abs{position:absolute}

/* top bar */
.topbar{left:0;top:0;width:1200px;height:43px;background:var(--dark);color:#ddd;font-size:12px;display:flex;align-items:center;justify-content:space-between;padding:0 95px}
.topbar nav{display:flex;gap:32px}

/* header */
.brand{left:95px;top:88px;display:flex;align-items:center;gap:14px}
.brand .mark{width:40px;height:40px;background:var(--dark)}
.brand .name{font-size:30px;font-weight:700;color:var(--dark);letter-spacing:.5px}
.mainnav{right:95px;top:96px;display:flex;gap:24px;font-size:12px;font-weight:700;color:var(--dark);text-transform:uppercase;align-items:center}
.mainnav .sep{width:1px;height:16px;background:var(--line)}

/* hero */
.greet{left:90px;top:169px;width:297px;height:311px;background:var(--teal);color:#fff;text-align:center;padding-top:26px}
.greet h2{font-size:28px;font-weight:800}
.greet .avatar{width:110px;height:110px;border-radius:50%;background:radial-gradient(circle,#f4d4c2,#c9a08c);margin:14px auto 10px}
.greet p{font-size:13px;font-weight:700;line-height:1.4;padding:0 30px}
.greet .btn{display:inline-block;margin-top:10px;background:var(--dark);color:#fff;font-weight:700;font-size:13px;padding:8px 18px}
.hero{left:428px;top:169px;width:674px;height:311px;background:linear-gradient(100deg,#b69a7e 0%,#8a6a4f 40%,#4c3a2e 70%,#2c2520 100%)}
.hero .copy{position:absolute;right:28px;top:64px;color:#fff;width:260px}
.hero h1{font-size:32px;font-weight:800;line-height:1.05}
.hero p{font-size:13px;font-weight:700;margin-top:10px;line-height:1.5}
.hero .btn{display:inline-block;margin-top:18px;background:var(--teal);color:#fff;font-weight:700;font-size:13px;padding:7px 16px}

/* sidebar panels */
.panel{left:90px;width:297px;background:var(--panel);color:#ddd}
.panel .head{height:34px;background:var(--teal);color:#fff;font-weight:700;font-size:13px;display:flex;align-items:center;justify-content:space-between;padding-left:14px;text-transform:uppercase}
.panel .head .plus{width:34px;height:34px;background:var(--dark);display:flex;align-items:center;justify-content:center;font-size:22px}
.cats{list-style:none;padding:14px 16px}
.cats li{display:flex;align-items:center;gap:16px;height:37px;font-size:10px;font-weight:700;text-transform:uppercase;border-bottom:1px solid #5a5a5a}
.cats li:last-child{border:none}
.cats li .box{width:17px;height:17px;background:#666;color:#fff;display:flex;align-items:center;justify-content:center;font-size:13px}
.cats li.on{color:var(--teal)}
.cats li.on .box{background:var(--teal)}
.why{padding:10px 16px}
.why .item{display:flex;gap:16px;padding:16px 0;border-bottom:1px solid #5a5a5a}
.why .item:last-child{border:none}
.num{flex:none;width:28px;height:28px;background:var(--teal);color:#fff;font-weight:700;font-size:14px;display:flex;align-items:center;justify-content:center}
.why h4,.news h4{color:var(--teal);font-size:10px;font-weight:700;text-transform:uppercase}
.why small,.news small{display:block;color:#999;font-size:9px;margin:2px 0 6px}
.why p,.news p{font-size:10px;line-height:1.6;color:#ccc}
.tabs{display:flex;gap:2px;margin-right:4px}
.tabs span{background:#bbb;color:#333;font-size:10px;padding:2px 6px}
.news{padding:12px 16px}
.news .item{display:flex;gap:16px;padding:10px 0 14px;border-bottom:1px solid #5a5a5a}
.news .item:last-child{border:none}
.date{flex:none;width:28px}
.date b{display:block;background:var(--teal);color:#fff;text-align:center;font-size:12px;height:26px;line-height:26px}
.date i{display:block;background:#5c5c5c;color:#fff;text-align:center;font-style:normal;font-size:12px;height:24px;line-height:24px}
.ad{left:90px;top:1699px;width:297px;height:506px;background:linear-gradient(160deg,#c98a2e,#8a4b16 60%,#5a2d0e)}

/* section headings */
.sechead{left:428px;width:674px;height:32px;border-bottom:2px solid var(--line);display:flex;justify-content:space-between;align-items:flex-end}
.sechead h3{background:var(--teal);color:#fff;font-size:12px;font-weight:700;text-transform:uppercase;padding:8px 12px;height:32px}
.arrows{display:flex;gap:2px;margin-bottom:2px}
.arrows span{width:26px;height:26px;background:var(--dark);display:flex;align-items:center;justify-content:center}
.viewall{background:var(--dark);color:#fff;font-size:11px;font-weight:700;padding:6px 12px;margin-bottom:2px}

/* products */
.row{left:428px;width:674px;display:grid;grid-template-columns:repeat(3,1fr)}
.card{text-align:center;position:relative}
.card .pic{width:150px;height:125px;margin:0 auto}
.badge{position:absolute;top:-12px;right:22px;width:36px;height:36px;border-radius:50%;background:var(--orange);color:#fff;font-size:10px;font-weight:700;display:flex;align-items:center;justify-content:center}
.badge.big{font-size:14px}
.stars{color:#f0b429;font-size:11px;letter-spacing:2px;margin-top:12px}
.card h5{font-size:11px;font-weight:700;margin-top:6px}
.card p{font-size:10px;color:#666;line-height:1.45;margin-top:4px}
.price{color:var(--price);font-size:15px;font-weight:700;margin-top:6px}
.buy{display:inline-flex;margin-top:10px}
.buy span{background:var(--btn);color:#fff;font-size:10px;font-weight:700;padding:6px 12px}
.buy i{width:26px;background:var(--teal);display:flex;align-items:center;justify-content:center}
.wood1{background:linear-gradient(135deg,#b34b2f,#6b8a6a,#c28a3a)}
.wood2{background:linear-gradient(180deg,#6a8fa2 0%,#7a5a3a 40%,#5a3d26)}
.wood3{background:linear-gradient(135deg,#caa77a,#8aa8b0,#a57a4e)}
.rattan{background:radial-gradient(ellipse at 50% 60%,#5a4a3f,#2f2722 60%,#fff 72%)}
.lamp{background:linear-gradient(180deg,#efd9a8 0 35%,#fff 35% 45%,#b7a07a 45% 50%,#fff 50%)}
.ratlight{background:radial-gradient(ellipse at 50% 55%,#c8906a,#8a5235 60%,#fff 72%)}
.cabinet{background:linear-gradient(90deg,#7a4a2c,#a46a40,#5e3a22)}
.vitrine{background:linear-gradient(180deg,#6b3f1d,#b07a3a,#6b3f1d)}

/* brands */
.brands{left:428px;top:2174px;width:674px;height:60px;display:flex;justify-content:space-around;align-items:center;font-size:22px;font-weight:700;color:#444}

/* tweet */
.tweet{left:0;top:2286px;width:1200px;height:90px;background:var(--beige);display:flex;align-items:center;justify-content:center;gap:10px;font-size:13px;color:#444}
.tweet b{color:var(--teal-dark)}

/* footer */
.footer{left:0;top:2376px;width:1200px;height:204px;background:var(--dark);color:#ccc;display:flex;gap:0;padding:34px 112px 0}
.fcol{width:210px}
.fcol h6{color:#fff;font-size:12px;font-weight:700;text-transform:uppercase;margin-bottom:16px}
.fcol p{font-size:10px;line-height:1.6}
.fcol .more{margin-top:16px;font-size:10px;display:flex;align-items:center;gap:8px}
.fcol .more i{width:10px;height:10px;border-radius:50%;background:var(--teal)}
.signup{width:180px}
.signup .form{display:flex;margin-top:14px}
.signup .form span{background:#fff;color:#999;font-size:9px;padding:6px 8px;width:128px}
.signup .form b{background:var(--teal);color:#fff;font-size:9px;padding:6px 8px}
.band{left:0;top:2580px;width:1200px;height:57px;background:var(--teal);color:#fff;font-size:12px;display:flex;align-items:center;padding:0 112px}
.band .loc{display:flex;gap:26px;width:350px}
.band nav{display:flex;gap:24px;margin-left:0}
.social{margin-left:auto;display:flex;gap:8px}
.social span{width:24px;height:24px;background:#2b7f9a}
.legal{left:0;top:2673px;width:1200px;text-align:center;font-size:11px;line-height:1.5;color:#333}
.legal a{color:#2a6fb0;text-decoration:none}
.seals{left:220px;top:2752px;width:760px;display:flex;justify-content:space-between;align-items:center}
.seals span{height:30px;background:#d8d8d8;border-radius:4px}
</style>
</head>
<body>

<header class="topbar abs">
  <span>Merela, welcome to our online store!</span>
  <nav><span>Login</span><span>&#9679; My Account &#8964;</span><span>&#9632; 0 item</span><span>Checkout</span></nav>
</header>

<div class="brand abs"><span class="mark"></span><span class="name">LOMAVEREDA</span></div>
<nav class="mainnav abs">
  <span>Home</span><span>Shop by Brand</span><span>Top Sellers</span><span>Clearance</span><span>Help Center</span><span>My Favorites</span><span class="sep"></span>
  <svg width="12" height="12" viewBox="0 0 12 12"><circle cx="5" cy="5" r="3.6" fill="none" stroke="#3b3b3b" stroke-width="1.6"/><line x1="7.6" y1="7.6" x2="11" y2="11" stroke="#3b3b3b" stroke-width="1.6"/></svg>
</nav>

<section class="greet abs">
  <h2>HI MERELA!</h2>
  <div class="avatar" role="img" aria-label="Customer avatar illustration"></div>
  <p>accusantium laudantium unde perspiciatis ipsam sed</p>
  <span class="btn">Learn more</span>
</section>
<section class="hero abs" role="img" aria-label="Bedroom interior with bed and lamp">
  <div class="copy">
    <h1>ACCUSANTI LAUDANTIUM</h1>
    <p>PERSPICIATIS DOLORE TOTAM UNDE UNDE ET AUT ILLO AUT</p>
    <span class="btn">pre-order now</span>
  </div>
</section>

<aside class="panel abs" style="top:518px;height:226px">
  <div class="head">Shop by Category<span class="plus">+</span></div>
  <ul class="cats">
    <li class="on"><span class="box">+</span>Vintage Furniture</li>
    <li><span class="box">+</span>Rattan Set Outdoor and Indoor</li>
    <li><span class="box">+</span>Lamps and</li>
    <li><span class="box">+</span>Wooden Wall Decor</li>
  </ul>
</aside>

<aside class="panel abs" style="top:779px;height:523px">
  <div class="head">Why you choose us<span class="plus">+</span></div>
  <div class="why">
    <div class="item"><span class="num">1</span><div><h4>Perspiciatis ipsam</h4><small>Dolore totam</small><p>Enim accusantium laudantium laudantium perspiciatis ipsam sed doloremque ipsam totam unde</p></div></div>
    <div class="item"><span class="num">2</span><div><h4>Perspiciatis ipsam</h4><small>Dolore totam</small><p>Enim accusantium laudantium laudantium perspiciatis ipsam sed doloremque ipsam totam unde</p></div></div>
    <div class="item"><span class="num">3</span><div><h4>Perspiciatis ipsam</h4><small>Dolore totam</small><p>Enim accusantium laudantium laudantium perspiciatis ipsam sed doloremque ipsam totam unde</p></div></div>
    <div class="item"><span class="num">4</span><div><h4>Perspiciatis ipsam</h4><small>Dolore totam</small><p>Enim accusantium laudantium laudantium perspiciatis ipsam sed doloremque ipsam totam unde</p></div></div>
  </div>
</aside>

<aside class="panel abs" style="top:1338px;height:290px">
  <div class="head">News from blog<span style="display:flex;align-items:center"><span class="tabs"><span>MENU 2</span><span>MENU 3</span></span><span class="plus">+</span></span></div>
  <div class="news">
    <div class="item"><div class="date"><b>10</b><i>11</i></div><div><h4>Vintage rattan sets</h4><small>Dolore totam</small><p>Accusantium laudantium laudantium perspiciatis ipsam sed doloremque ipsam totam unde accusantium</p></div></div>
    <div class="item"><div class="date"><b>10</b><i>11</i></div><div><h4>Wooden wall decor</h4><small>Dolore totam</small><p>Accusantium laudantium laudantium perspiciatis ipsam sed doloremque ipsam totam unde accusantium</p></div></div>
  </div>
</aside>

<div class="ad abs" role="img" aria-label="Advertisement with carved wooden chair detail"></div>

<!-- new products -->
<div class="sechead abs" style="top:520px"><h3>New products of the week</h3>
  <div class="arrows"><span><svg width="8" height="10"><path d="M6 1 2 5l4 4" stroke="#fff" stroke-width="1.6" fill="none"/></svg></span><span><svg width="8" height="10"><path d="M2 1l4 4-4 4" stroke="#fff" stroke-width="1.6" fill="none"/></svg></span></div></div>
<div class="row abs" style="top:610px">
  <div class="card"><span class="badge">NEW</span><div class="pic wood1" role="img" aria-label="Painted vintage chest of drawers"></div><div class="stars">★★★★★</div><h5>REM IPSAM QUAS</h5><p>Enim accusantium laudantium<br>perspiciatis doloremque</p><div class="price">$ 987.00</div><div class="buy"><span>BUY NOW</span><i><svg width="14" height="12"><path d="M1 1h2l2 7h7l1-5H4" stroke="#fff" fill="none" stroke-width="1.4"/><circle cx="6" cy="10.5" r="1" fill="#fff"/><circle cx="11" cy="10.5" r="1" fill="#fff"/></svg></i></div></div>
  <div class="card"><span class="badge">NEW</span><div class="pic wood2" role="img" aria-label="Reclaimed wood console table"></div><div class="stars">★★★★★</div><h5>REM IPSAM QUAS</h5><p>Enim accusantium laudantium<br>perspiciatis doloremque</p><div class="price">$ 987.00</div><div class="buy"><span>BUY NOW</span><i><svg width="14" height="12"><path d="M1 1h2l2 7h7l1-5H4" stroke="#fff" fill="none" stroke-width="1.4"/><circle cx="6" cy="10.5" r="1" fill="#fff"/><circle cx="11" cy="10.5" r="1" fill="#fff"/></svg></i></div></div>
  <div class="card"><span class="badge">NEW</span><div class="pic wood3" role="img" aria-label="Distressed wooden sideboard"></div><div class="stars">★★★★★</div><h5>REM IPSAM QUAS</h5><p>Enim accusantium laudantium<br>perspiciatis doloremque</p><div class="price">$ 987.00</div><div class="buy"><span>BUY NOW</span><i><svg width="14" height="12"><path d="M1 1h2l2 7h7l1-5H4" stroke="#fff" fill="none" stroke-width="1.4"/><circle cx="6" cy="10.5" r="1" fill="#fff"/><circle cx="11" cy="10.5" r="1" fill="#fff"/></svg></i></div></div>
</div>

<!-- bestsellers -->
<div class="sechead abs" style="top:936px"><h3>Bestseller products</h3>
  <div class="arrows"><span><svg width="8" height="10"><path d="M6 1 2 5l4 4" stroke="#fff" stroke-width="1.6" fill="none"/></svg></span><span><svg width="8" height="10"><path d="M2 1l4 4-4 4" stroke="#fff" stroke-width="1.6" fill="none"/></svg></span></div></div>
<div class="row abs" style="top:1024px">
  <div class="card"><span class="badge big">50.</span><div class="pic rattan" role="img" aria-label="Dark rattan dining set"></div><div class="stars">★★★★★</div><h5>REM IPSAM QUAS</h5><p>Enim accusantium laudantium<br>perspiciatis doloremque</p><div class="price">$ 987.00</div><div class="buy"><span>BUY NOW</span><i><svg width="14" height="12"><path d="M1 1h2l2 7h7l1-5H4" stroke="#fff" fill="none" stroke-width="1.4"/><circle cx="6" cy="10.5" r="1" fill="#fff"/><circle cx="11" cy="10.5" r="1" fill="#fff"/></svg></i></div></div>
  <div class="card"><span class="badge big">20.</span><div class="pic lamp" role="img" aria-label="Floor lamp with cream shade"></div><div class="stars">★★★★★</div><h5>REM IPSAM QUAS</h5><p>Enim accusantium laudantium<br>perspiciatis doloremque</p><div class="price">$ 987.00</div><div class="buy"><span>BUY NOW</span><i><svg width="14" height="12"><path d="M1 1h2l2 7h7l1-5H4" stroke="#fff" fill="none" stroke-width="1.4"/><circle cx="6" cy="10.5" r="1" fill="#fff"/><circle cx="11" cy="10.5" r="1" fill="#fff"/></svg></i></div></div>
  <div class="card"><div class="pic ratlight" role="img" aria-label="Round rattan lounge set"></div><div class="stars">★★★★★</div><h5>REM IPSAM QUAS</h5><p>Enim accusantium laudantium<br>perspiciatis doloremque</p><div class="price">$ 987.00</div><div class="buy"><span>BUY NOW</span><i><svg width="14" height="12"><path d="M1 1h2l2 7h7l1-5H4" stroke="#fff" fill="none" stroke-width="1.4"/><circle cx="6" cy="10.5" r="1" fill="#fff"/><circle cx="11" cy="10.5" r="1" fill="#fff"/></svg></i></div></div>
</div>

<!-- featured -->
<div class="sechead abs" style="top:1349px"><h3>Featured products</h3><span class="viewall">view all</span></div>
<div class="row abs" style="top:1428px">
  <div class="card"><div class="pic cabinet" role="img" aria-label="Wooden cabinet with open door"></div><div class="stars">★★★★★</div><h5>REM IPSAM QUAS</h5><p>Enim accusantium laudantium<br>perspiciatis doloremque</p><div class="price">$ 987.00</div><div class="buy"><span>BUY NOW</span><i><svg width="14" height="12"><path d="M1 1h2l2 7h7l1-5H4" stroke="#fff" fill="none" stroke-width="1.4"/><circle cx="6" cy="10.5" r="1" fill="#fff"/><circle cx="11" cy="10.5" r="1" fill="#fff"/></svg></i></div></div>
  <div class="card"><div class="pic wood1" role="img" aria-label="Painted vintage chest of drawers"></div><div class="stars">★★★★★</div><h5>REM IPSAM QUAS</h5><p>Enim accusantium laudantium<br>perspiciatis doloremque</p><div class="price">$ 987.00</div><div class="buy"><span>BUY NOW</span><i><svg width="14" height="12"><path d="M1 1h2l2 7h7l1-5H4" stroke="#fff" fill="none" stroke-width="1.4"/><circle cx="6" cy="10.5" r="1" fill="#fff"/><circle cx="11" cy="10.5" r="1" fill="#fff"/></svg></i></div></div>
  <div class="card"><div class="pic vitrine" role="img" aria-label="Tall wooden display cabinet"></div><div class="stars">★★★★★</div><h5>REM IPSAM QUAS</h5><p>Enim accusantium laudantium<br>perspiciatis doloremque</p><div class="price">$ 987.00</div><div class="buy"><span>BUY NOW</span><i><svg width="14" height="12"><path d="M1 1h2l2 7h7l1-5H4" stroke="#fff" fill="none" stroke-width="1.4"/><circle cx="6" cy="10.5" r="1" fill="#fff"/><circle cx="11" cy="10.5" r="1" fill="#fff"/></svg></i></div></div>
</div>
<div class="row abs" style="top:1808px">
  <div class="card"><div class="pic ratlight" role="img" aria-label="Round rattan lounge set"></div><div class="stars">★★★★★</div><h5>REM IPSAM QUAS</h5><p>Enim accusantium laudantium<br>perspiciatis doloremque</p><div class="price">$ 987.00</div><div class="buy"><span>BUY NOW</span><i><svg width="14" height="12"><path d="M1 1h2l2 7h7l1-5H4" stroke="#fff" fill="none" stroke-width="1.4"/><circle cx="6" cy="10.5" r="1" fill="#fff"/><circle cx="11" cy="10.5" r="1" fill="#fff"/></svg></i></div></div>
  <div class="card"><div class="pic wood3" role="img" aria-label="Distressed wooden sideboard"></div><div class="stars">★★★★★</div><h5>REM IPSAM QUAS</h5><p>Enim accusantium laudantium<br>perspiciatis doloremque</p><div class="price">$ 987.00</div><div class="buy"><span>BUY NOW</span><i><svg width="14" height="12"><path d="M1 1h2l2 7h7l1-5H4" stroke="#fff" fill="none" stroke-width="1.4"/><circle cx="6" cy="10.5" r="1" fill="#fff"/><circle cx="11" cy="10.5" r="1" fill="#fff"/></svg></i></div></div>
  <div class="card"><div class="pic rattan" role="img" aria-label="Dark rattan dining set"></div><div class="stars">★★★★★</div><h5>REM IPSAM QUAS</h5><p>Enim accusantium laudantium<br>perspiciatis doloremque</p><div class="price">$ 987.00</div><div class="buy"><span>BUY NOW</span><i><svg width="14" height="12"><path d="M1 1h2l2 7h7l1-5H4" stroke="#fff" fill="none" stroke-width="1.4"/><circle cx="6" cy="10.5" r="1" fill="#fff"/><circle cx="11" cy="10.5" r="1" fill="#fff"/></svg></i></div></div>
</div>

<!-- brands -->
<div class="sechead abs" style="top:2107px"><h3>Search by brand</h3>
  <div class="arrows"><span><svg width="8" height="10"><path d="M6 1 2 5l4 4" stroke="#fff" stroke-width="1.6" fill="none"/></svg></span><span><svg width="8" height="10"><path d="M2 1l4 4-4 4" stroke="#fff" stroke-width="1.6" fill="none"/></svg></span></div></div>
<div class="brands abs"><span>Tarvik</span><span>Olmo</span><span>Brenta</span><span>Kavell</span><span>Ludra</span></div>

<div class="tweet abs">
  <svg width="18" height="16" viewBox="0 0 18 16"><circle cx="9" cy="8" r="7" fill="#1fb5a8"/></svg>
  <span>“I have never met a designer who was retained to keep things the same as they were.” - <b>Harlan Voss http://lnk.to/vx4Rm #WHYVW</b></span>
</div>

<footer class="footer abs">
  <div class="fcol"><h6>Who we are?</h6><p>Fugit illo omnis explicabo<br>ipsa, nemo ipsam quia<br>voluptas dolor perspiciatis<br>beatae magni architecto</p><div class="more">Read more <i></i></div></div>
  <div class="fcol"><h6>What we sell?</h6><p>Omnis explicabo<br>Nemo ipsam quia<br>Voluptatem dolor<br>Beatae magni archite<br>Odit nemo ipsam quasi</p><div class="more">Read more <i></i></div></div>
  <div class="fcol"><h6>Shipping</h6><p>Fugit illo omnis explicabo<br>ipsa, nemo ipsam quia<br>voluptas dolor perspiciatis<br>beatae magni architecto</p><div class="more">Read more <i></i></div></div>
  <div class="fcol"><h6>Track your order</h6><p>Omnis explicabo<br>Nemo ipsam quia<br>Voluptatem dolor<br>Beatae magni archite<br>Odit nemo ipsam quasi</p><div class="more">Read more <i></i></div></div>
  <div class="fcol signup"><h6>Sign up for special deals!</h6><p>Get exclusive access to expert tips, special offers and coupons.</p><div class="form"><span>enter your email address</span><b>Sign Up</b></div></div>
</footer>

<div class="band abs">
  <div class="loc"><span>United States - English &#8964;</span><span>Currency USD &#8964;</span></div>
  <nav><span>Home</span><span>About Us</span><span>Privacy Policy</span><span>Contact Us</span></nav>
  <div class="social"><span></span><span></span><span></span><span></span><span></span><span></span></div>
</div>

<p class="legal abs">Use of this Site is subject to express terms of use. By using this site, you signify that you agree<br>to be bound by these <a>Universal Terms of Service</a>, <a>Legal Privacy Policy</a><br>Copyright © 2014 Your Company. All Rights Reserved.</p>

<div class="seals abs">
  <span style="width:70px"></span><span style="width:56px"></span><span style="width:110px"></span><span style="width:50px"></span><span style="width:40px"></span><span style="width:44px"></span><span style="width:124px"></span>
</div>

</body>
</html>
```